Business Card for premium dental clinic

We are a premium dental clinic based in Brasov, Romania with more than 15 year on the market, providing quality dental treatment made by a team of more specialized dentists, working with modern equipment as a solution to beautiful and healthy teeth.

Our current logo for the clinic use 2 square with colors black and gold - dr Ternisu - studio, using family fonts Bodoni, Myriad Pro and Segoe Print.
Depending on the printing we used some gold CMYK background or gold foil picture background or a gold gradient.
We want a business card:
- eye catching business card
- distinguished business card
- premium design
- to keep the color scheme of black and gold
- to attract the customers to spent time reading the information
- modern concept

```html
<!DOCTYPE html>
<html lang="en">
<head>
<meta charset="utf-8">
<title>Business Card – dr Ternisu</title>
<link href="https://fonts.googleapis.com/css2?family=Roboto:wght@400;500;700&family=Ubuntu:wght@700&display=swap" rel="stylesheet">
<style>
  :root {
    --backdrop: #a88c6e;
    --card: #f4f3ef;
    --ink: #2b2b2b;
    --ink-strong: #111111;
    --gold: #b8942c;
    --gold-light: #e2c25a;
    --gold-deep: #a07e22;
    --rule: #333333;
  }
  * { box-sizing: border-box; margin: 0; padding: 0; }
  html, body {
    width: 1200px;
    height: 900px;
    overflow: hidden;
  }
  body {
    background: var(--backdrop);
    font-family: "Roboto", Arial, sans-serif;
    position: relative;
  }
  .business-card {
    position: absolute;
    left: 100px;
    top: 164px;
    width: 1000px;
    height: 572px;
    background: var(--card);
    box-shadow: 0 14px 30px rgba(0, 0, 0, 0.25);
  }
  .brand {
    position: absolute;
    left: 110px;
    top: 236px;
    display: flex;
    align-items: center;
    gap: 22px;
  }
  .brand-square {
    width: 96px;
    height: 96px;
    background: linear-gradient(135deg, var(--gold-light), var(--gold) 55%, var(--gold-deep));
  }
  .brand-name {
    font-family: "Roboto", Arial, sans-serif;
    font-weight: 400;
    font-size: 52px;
    color: var(--ink-strong);
    letter-spacing: 0.5px;
  }
  .divider {
    position: absolute;
    left: 590px;
    top: 118px;
    width: 2px;
    height: 336px;
    background: var(--rule);
  }
  .contact {
    position: absolute;
    left: 630px;
    top: 112px;
    color: var(--ink);
  }
  .contact-name {
    font-family: "Ubuntu", Arial, sans-serif;
    font-weight: 700;
    font-size: 34px;
    color: var(--gold);
    letter-spacing: 0.5px;
  }
  .contact-title {
    font-weight: 700;
    font-size: 19px;
    color: var(--ink-strong);
    margin-top: 6px;
  }
  .contact-address {
    font-size: 20px;
    line-height: 28px;
    margin-top: 26px;
  }
  .contact-lines {
    list-style: none;
    font-size: 20px;
    line-height: 26px;
    margin-top: 30px;
  }
  .contact-web {
    font-size: 20px;
    color: var(--gold);
    margin-top: 30px;
  }
</style>
</head>
<body>
  <main class="business-card">
    <div class="brand">
      <span class="brand-square" aria-hidden="true"></span>
      <span class="brand-name">dr Ternisu</span>
    </div>

    <div class="divider" aria-hidden="true"></div>

    <section class="contact">
      <h1 class="contact-name">Andrei Moraru</h1>
      <p class="contact-title">President</p>
      <p class="contact-address">14 Livada Street<br>Brasov, Romania 500123</p>
      <ul class="contact-lines">
        <li>P. 268-410-2273</li>
        <li>C. 268-735-9016</li>
        <li>F. 268-410-2274</li>
        <li>hello@ternisuclinic.ro</li>
      </ul>
      <p class="contact-web">www.ternisuclinic.ro</p>
    </section>
  </main>
</body>
</html>
```